Business card

We need a business card design for our company based in Auckland , New Zealand called 'Ridge + Studio Ltd'. We provide architectural services. We would like to see designs that use the max. three colours (such as white, black, grey) The final design should communicate financial safety and growth."
Also I will provide our company logo. I would like to the logo to be embeded onto our business card.

Target Market(s)

new residential house, alteration & addition & light commericila design & drafting service

Industry/Entity Type

Architecture

Contact Information for Business Card

Company name: ridge + studio Ltd.
Name: Mark Delford
Job title: architectural designer & Design LBP
email address: mark@rplusd.co.nz
mobile number: 02 5163 2290
web site: www.rplusd.co.nz

Requirements
Must have
• My project must have..
• - embeded logo (attached company logo)
• I don't have a bigger version for our company logo, but I have one old one, so you can remove the word from it)
• - insert the attached small BKTW logo & LBP logo
• - creative, simple and clear business card.
• - Max. three colours
Nice to have
• - Here are the samples I would like to share with you: http://www.plimvora.com/blog/minimalistic-business-card-designs/
• I would like to have my business card like one of the creation.
Should not have
• TBA

```html
<!DOCTYPE html>
<html lang="en">
<head>
<meta charset="utf-8">
<title>Ridge + Studio Ltd — Business Card</title>
<link rel="stylesheet" href="https://fonts.googleapis.com/css2?family=Arimo:wght@400;700&display=swap">
<style>
  :root {
    --backdrop: #e6e6e6;
    --paper: #ffffff;
    --ink: #0b0b0b;
    --mid-grey: #5a5a5a;
    --soft-grey: #8a8a8a;
    --pale-grey: #d9d9d9;
    --text-on-dark: #f2f2f2;
  }
  * { margin: 0; padding: 0; box-sizing: border-box; }
  html, body { width: 1200px; height: 950px; overflow: hidden; }
  body {
    background: var(--backdrop);
    font-family: "Arimo", Arial, sans-serif;
    position: relative;
  }
  .card {
    position: absolute;
    width: 640px;
    height: 366px;
    left: 280px;
    box-shadow: 0 6px 18px rgba(0,0,0,0.18);
    overflow: hidden;
  }

  /* Front side */
  .card--front { top: 70px; background: var(--paper); }
  .front-marks {
    position: absolute;
    left: 0; right: 0; top: 118px;
    display: flex;
    align-items: center;
    justify-content: center;
    gap: 26px;
  }
  .association-name {
    font-size: 44px;
    font-weight: 700;
    color: var(--mid-grey);
    letter-spacing: -1px;
  }
  .marks-divider { width: 1px; height: 96px; background: var(--soft-grey); }
  .practitioner-badge {
    width: 96px; height: 96px;
    border-radius: 50%;
    background: var(--mid-grey);
  }
  .front-web {
    position: absolute;
    left: 0; right: 0; top: 292px;
    text-align: center;
    font-size: 15px;
    color: var(--soft-grey);
  }

  /* Back side */
  .card--back { top: 510px; background: var(--ink); }
  .back-art-area {
    position: absolute;
    left: 330px; top: 110px; right: 0; bottom: 0;
    background: linear-gradient(135deg, var(--pale-grey) 0%, var(--paper) 45%, var(--paper) 100%);
  }
  .holder {
    position: absolute;
    left: 44px; top: 30px;
    color: var(--text-on-dark);
    font-size: 18px;
    font-weight: 700;
    line-height: 1.3;
  }
  .holder-title { margin-top: 2px; }
  .contact {
    position: absolute;
    left: 44px; top: 156px;
    list-style: none;
    color: var(--text-on-dark);
    font-size: 13px;
    line-height: 1.45;
  }
  .brand {
    position: absolute;
    left: 390px; top: 222px;
    display: flex;
    align-items: center;
    gap: 10px;
  }
  .brand-dot {
    width: 18px; height: 18px;
    border: 3px solid var(--ink);
    border-radius: 50%;
  }
  .brand-name { font-size: 22px; font-weight: 700; color: var(--ink); }
</style>
</head>
<body>

  <section class="card card--front" aria-label="Card front">
    <div class="front-marks">
      <span class="association-name">BKTW</span>
      <span class="marks-divider"></span>
      <span class="practitioner-badge" role="img" aria-label="Licensed practitioner badge"></span>
    </div>
    <p class="front-web">www.rplusd.co.nz</p>
  </section>

  <section class="card card--back" aria-label="Card back">
    <div class="back-art-area" role="img" aria-label="Decorative light panel behind the company name"></div>

    <div class="holder">
      <p class="holder-name">Mark Delford</p>
      <p class="holder-title">architectural designer &amp;<br>Design LBP</p>
    </div>

    <ul class="contact">
      <li>Ridge + Studio Ltd</li>
      <li>M : 02 5163 2290</li>
      <li>E : mark@rplusd.co.nz</li>
      <li>W : www.rplusd.co.nz</li>
    </ul>

    <div class="brand">
      <span class="brand-dot"></span>
      <span class="brand-name">ridge + studio</span>
    </div>
  </section>

</body>
</html>
```